Car transport business

We need a new business card design. Attached is our old card sample. I would just like to adjust the logo colors (blue and red) to be brighter. I changed my name to the brighter red and the word dispatcher to a brighter blue as an example. But you can adjust those colors further. And then perhaps you can use the same colors for the card design but use your imagination.

As a suggestion so the card stands out I would like to add a clip art of car carrier truck. Attached are examples of that as well

```html
<!DOCTYPE html>
<html lang="en">
<head>
<meta charset="utf-8">
<title>Apex Haul – Business Card</title>
<link href="https://fonts.googleapis.com/css2?family=Montserrat:wght@400;500;700&display=swap" rel="stylesheet">
<style>
  :root {
    --page-bg: #dddddd;
    --card-white: #ffffff;
    --brand-blue: #175a87;
    --brand-red: #c01f2d;
    --back-blue: #165a86;
    --back-ink: #0f3f60;
    --back-accent: #3aa0e6;
  }
  * { margin: 0; padding: 0; box-sizing: border-box; }
  html, body {
    width: 1200px; height: 1200px; overflow: hidden;
    background: var(--page-bg);
    font-family: "Montserrat", sans-serif;
  }
  .card {
    position: absolute; left: 207px; width: 786px; height: 449px;
  }
  .card-front { top: 112px; background: var(--card-white); }
  .card-back { top: 640px; background: var(--back-blue); }

  .brand { position: absolute; display: flex; align-items: center; gap: 14px; }
  .brand-dot { width: 40px; height: 40px; border-radius: 50%; }
  .brand-name { font-weight: 700; letter-spacing: 2px; line-height: 1; }

  .card-front .brand { left: 190px; top: 136px; }
  .card-front .brand-dot { background: var(--brand-red); }
  .card-front .brand-name { font-size: 46px; color: var(--brand-blue); }

  .card-back .brand { left: 180px; top: 200px; }
  .card-back .brand-dot { background: var(--back-accent); width: 46px; height: 46px; }
  .card-back .brand-name { font-size: 56px; color: var(--back-ink); }

  .person {
    position: absolute; right: calc(786px - 346px); top: 296px; text-align: right;
  }
  .person-name {
    font-size: 40px; font-weight: 500; color: var(--brand-red); line-height: 1; letter-spacing: 0.5px;
  }
  .person-role {
    font-size: 20px; color: var(--brand-blue); line-height: 1; margin-top: 8px; letter-spacing: 0.5px;
  }
  .divider {
    position: absolute; left: 372px; top: 296px; width: 1.5px; height: 67px; background: var(--brand-red);
  }
  .contacts { position: absolute; left: 394px; top: 294px; list-style: none; }
  .contacts li {
    display: flex; align-items: center; gap: 6px; height: 25px;
    font-size: 19.5px; color: var(--brand-blue);
  }
  .contacts svg { width: 16px; height: 16px; fill: var(--brand-red); flex: none; }
</style>
</head>
<body>
  <section class="card card-front">
    <div class="brand">
      <span class="brand-dot"></span>
      <span class="brand-name">APEX HAUL</span>
    </div>

    <div class="person">
      <p class="person-name">MILO VARGA</p>
      <p class="person-role">DISPATCHER</p>
    </div>
    <div class="divider"></div>
    <ul class="contacts">
      <li>
        <svg viewBox="0 0 16 16" aria-hidden="true"><path d="M4 1l2.5 3-1.3 1.6c.8 1.9 2.2 3.5 4.1 4.6L11 9l3 2.4-1.4 2.8C7.4 13.6 2.7 8.9 2 3.3z"/></svg>
        <span>555-014-2290</span>
      </li>
      <li>
        <svg viewBox="0 0 16 16" aria-hidden="true"><path d="M4 1h7l1 1v3H4zM1 6h14v6h-3v3H4v-3H1zm4 4v4h6v-4z"/></svg>
        <span>555-014-7731</span>
      </li>
      <li>
        <svg viewBox="0 0 16 16" aria-hidden="true"><path d="M1 3h14v10H1zm1.5 1.5v.4L8 8.6l5.5-3.7v-.4zm0 2.2v4.8h11V6.7L8 10.4z"/></svg>
        <span>apexhaulco@mail.com</span>
      </li>
    </ul>
  </section>

  <section class="card card-back">
    <div class="brand">
      <span class="brand-dot"></span>
      <span class="brand-name">APEX HAUL</span>
    </div>
  </section>
</body>
</html>
```